Build PowerPoint for New Logo & Letterhead

I have started my own consulting firm and created a logo and letterhead (attached) am looking PowerPoint template. My name is Dorrit Vandermolen and the company is called K Quadrant Advisory. We primarily use PowerPoint files to display analyses, maps and key talking points from interviews and/or recommendations. We use the documents more to facilitate discussion with our target audiences. Most of the time our PowerPoint document is printed as handouts for our clients and not projected.

Target Market(s)

Healthcare provider organizations (hospitals, health systems, physician groups)

Industry/Entity Type

Healthcare

Font styles to use
Sans Serif

Colors
abd036
1f9ad1
0355a3

Requirements
Must have
• I would like to cover page to play off of the letterhead in some fashion. I want the design to provide plenty of space for text, graphics, maps, pictures, etc.
• We will usually include our clients logo somewhere on the document. Historically it is prominent on the cover page and then in one of the corners on all of the pages thereafter.

```html
<!DOCTYPE html>
<html lang="en">
<head>
<meta charset="utf-8">
<title>K Quadrant Advisory – Presentation Template</title>
<link href="https://fonts.googleapis.com/css2?family=Open+Sans:wght@400;600;700&display=swap" rel="stylesheet">
<style>
:root{
  --green:#abd036;
  --sky:#1f9ad1;
  --navy:#0355a3;
  --charcoal:#58595b;
  --grey:#9a9b9d;
  --pale:#ececec;
  --page:#e6e7e8;
  --ink:#3a3a3a;
}
*{box-sizing:border-box;margin:0;padding:0}
html,body{width:905px;height:1200px;overflow:hidden;background:var(--page);font-family:'Open Sans',Arial,sans-serif;color:var(--ink)}
.sheet{display:grid;grid-template-columns:repeat(3,285px);grid-auto-rows:159px;gap:9px 10px;padding:17px 15px}
.slide{position:relative;background:#fff;overflow:hidden;box-shadow:0 1px 3px rgba(0,0,0,.25)}
.abs{position:absolute}
.brand{font-weight:700;color:var(--navy);line-height:1.1}
.header{position:absolute;left:0;top:0;width:285px;height:24px}
.header-title{position:absolute;left:52px;top:7px;font-size:9px;font-weight:700;color:#fff}
.header-brand{position:absolute;left:6px;top:8px;font-size:4px;width:26px}
.footer{position:absolute;left:0;bottom:0;width:285px;height:14px}
.client{position:absolute;right:6px;bottom:7px;font-size:4.2px;font-weight:700;color:#222}
.copy{position:absolute;left:112px;bottom:4px;font-size:2.6px;color:#999}
.h4{font-size:5.5px;font-weight:700;color:var(--sky);margin-bottom:2px}
.txt{font-size:4.2px;line-height:1.35;color:#555}
ul.bullets{list-style:none}
ul.bullets li{font-size:4.2px;line-height:1.35;color:#555;padding-left:4px;position:relative;margin-bottom:1px}
ul.bullets li:before{content:"•";position:absolute;left:0}
ul.bullets li.sub{padding-left:9px;color:#777}
ul.bullets li.sub:before{content:"–";left:5px}
.photo{position:absolute;background:linear-gradient(135deg,#dfe5ea,#b9c3cc 60%,#8d9aa6)}
.photo-blue{background:linear-gradient(135deg,#2aa4dd,#1f9ad1 50%,#1a7fc0)}
.photo-dark{background:linear-gradient(135deg,#7f8a93,#5c666f 55%,#3f464d)}
.big-title{font-weight:700;color:#111}
.num-circle{width:15px;height:15px;border:1.3px solid var(--green);border-radius:50%;font-size:6px;font-weight:700;color:var(--navy);display:flex;align-items:center;justify-content:center}
.toc-item{position:absolute;width:80px}
.toc-item .label{position:absolute;left:22px;top:4px;font-size:4.5px;font-weight:700}
.toc-item .txt{position:absolute;left:2px;top:20px;width:75px}
.member{position:absolute;width:40px;text-align:center}
.member .avatar{width:28px;height:28px;border-radius:50%;margin:0 auto;border:1.3px solid var(--green);background:linear-gradient(135deg,#e3e8ec,#aab5bf)}
.member .name{font-size:4.5px;font-weight:700;font-style:italic;color:var(--sky);margin-top:2px}
.member .role{font-size:3.4px;color:#888}
table.data{position:absolute;left:13px;top:31px;width:259px;border-collapse:collapse;font-size:3.2px;color:#666}
table.data th{color:#fff;font-size:4.3px;font-weight:600;height:12px;text-align:left;padding-left:5px}
table.data td{padding:2px 4px;vertical-align:top;height:16px}
table.data tr:nth-child(odd) td{background:var(--pale)}
.icon-card{position:absolute;width:55px;text-align:center}
.icon-card .dot{width:20px;height:20px;border-radius:50%;background:#fff;margin:0 auto 3px;display:flex;align-items:center;justify-content:center}
.icon-card .h{font-size:4.5px;font-weight:700;color:var(--sky)}
.icon-card .t{font-size:3.4px;color:#666;line-height:1.3}
.center-copy{position:absolute;text-align:center;color:#fff}
</style>
</head>
<body>
<main class="sheet">

<!-- 1 cover -->
<section class="slide">
  <div class="photo photo-blue" style="inset:0" role="img" aria-label="Blue-toned photo of people walking through a bright hospital corridor"></div>
  <div class="center-copy" style="left:40px;top:53px;width:205px;font-size:4.8px;line-height:1.35">
    <b>Lorem ipsum</b> dolor sit amet, consectetur adipiscing elit. Suspendisse eget ligula mollis, mattis libero eget, rutrum ipsum.
    <div style="font-size:3.2px;margin-top:4px;opacity:.85">Copyright © 2016 K Quadrant Advisory All rights reserved.</div>
  </div>
  <div class="center-copy" style="left:90px;top:100px;width:105px;font-size:7px;font-weight:700">K Quadrant Advisory</div>
</section>

<!-- 2 title -->
<section class="slide">
  <svg class="abs" style="left:0;top:0" width="285" height="159" viewBox="0 0 285 159">
    <polyline points="0,102 160,102 178,112 285,112" fill="none" stroke="var(--green)" stroke-width="2.5"/>
    <polyline points="0,106 155,106 174,117 285,117" fill="none" stroke="var(--sky)" stroke-width="1.5"/>
    <polygon points="176,113 285,113 285,118 182,118" fill="var(--navy)"/>
  </svg>
  <div class="abs big-title" style="left:7px;top:113px;font-size:12px">Presentation Title</div>
  <div class="abs" style="left:7px;top:129px;font-size:6.3px">Subheading Presentation Title</div>
  <div class="abs" style="left:7px;top:145px;font-size:4px">May 2016</div>
  <div class="abs brand" style="left:236px;top:134px;font-size:5px;width:44px;text-align:right">K Quadrant Advisory</div>
</section>

<!-- 3 title alt -->
<section class="slide">
  <div class="abs big-title" style="left:15px;top:44px;font-size:13px">Presentation Title</div>
  <div class="abs" style="left:15px;top:62px;font-size:6.5px">Subheading Presentation Title</div>
  <div class="abs" style="left:15px;top:78px;font-size:4px">May 2016</div>
  <svg class="abs" style="left:0;top:0" width="285" height="159" viewBox="0 0 285 159">
    <polyline points="0,112 50,112 58,118 285,118" fill="none" stroke="var(--green)" stroke-width="2"/>
    <polyline points="0,115 48,115 56,121 285,121" fill="none" stroke="var(--sky)" stroke-width="1.2"/>
  </svg>
  <div class="abs brand" style="left:14px;top:134px;font-size:4.5px;width:30px">K Quadrant Advisory</div>
  <div class="abs" style="left:52px;top:134px;font-size:3.8px;color:var(--sky);line-height:2.2">Email: dorrit@kquadrantadvisory.co<br>Telephone: 555.014.2290</div>
  <div class="client">client logo here</div>
</section>

<!-- 4 section -->
<section class="slide">
  <svg class="abs" style="left:0;top:0" width="285" height="159" viewBox="0 0 285 159">
    <polyline points="0,116 95,116 113,132 285,132" fill="none" stroke="var(--green)" stroke-width="2.5"/>
    <polyline points="0,120 92,120 110,136 285,136" fill="none" stroke="var(--sky)" stroke-width="1.4"/>
    <polygon points="108,133 285,133 285,138 114,138" fill="var(--navy)"/>
  </svg>
  <div class="abs" style="left:7px;top:126px;font-size:8.5px;font-weight:700;color:#111">Section Slide</div>
  <div class="abs" style="left:7px;top:139px;font-size:5.5px">Divider Presentation Title</div>
</section>

<!-- 5 toc -->
<section class="slide">
  <svg class="header" viewBox="0 0 285 24"><polygon points="40,4 285,4 285,20 32,20" fill="var(--charcoal)"/><rect x="272" y="6" width="8" height="6" fill="var(--sky)"/><rect x="0" y="21" width="285" height="1" fill="var(--sky)"/></svg>
  <div class="header-brand brand">K Quadrant</div>
  <div class="header-title">Table of Content</div>
  <div class="toc-item" style="left:18px;top:38px"><div class="num-circle">1</div><div class="label">Lorem Ipsum</div><div class="txt">Lorem ipsum dolor sit amet, te ullum corpora delicata duo. Rebum insolens pri eu.</div></div>
  <div class="toc-item" style="left:107px;top:38px"><div class="num-circle">2</div><div class="label">Lorem Ipsum</div><div class="txt">Lorem ipsum dolor sit amet, te ullum corpora delicata duo. Rebum insolens pri eu.</div></div>
  <div class="toc-item" style="left:192px;top:38px"><div class="num-circle">3</div><div class="label">Lorem Ipsum</div><div class="txt">Lorem ipsum dolor sit amet, te ullum corpora delicata duo. Rebum insolens pri eu.</div></div>
  <div class="toc-item" style="left:18px;top:92px"><div class="num-circle">4</div><div class="label">Lorem Ipsum</div><div class="txt">Lorem ipsum dolor sit amet, te ullum corpora delicata duo. Rebum insolens pri eu.</div></div>
  <div class="toc-item" style="left:107px;top:92px"><div class="num-circle">5</div><div class="label">Lorem Ipsum</div><div class="txt">Lorem ipsum dolor sit amet, te ullum corpora delicata duo. Rebum insolens pri eu.</div></div>
  <div class="toc-item" style="left:192px;top:92px"><div class="num-circle">6</div><div class="label">Lorem Ipsum</div><div class="txt">Lorem ipsum dolor sit amet, te ullum corpora delicata duo. Rebum insolens pri eu.</div></div>
  <svg class="footer" viewBox="0 0 285 14"><polyline points="0,11 200,11 208,13 285,13" fill="none" stroke="var(--green)" stroke-width="1.2"/><polyline points="0,13 285,13" fill="none" stroke="var(--sky)" stroke-width=".8"/></svg>
  <div class="copy">Copyright © 2016 K Quadrant Advisory All rights reserved.</div>
  <div class="client">client logo here</div>
</section>

<!-- 6 one column -->
<section class="slide">
  <svg class="header" viewBox="0 0 285 24"><polygon points="40,4 285,4 285,20 32,20" fill="var(--charcoal)"/><rect x="272" y="6" width="8" height="6" fill="var(--sky)"/><rect x="0" y="21" width="285" height="1" fill="var(--sky)"/></svg>
  <div class="header-brand brand">K Quadrant</div>
  <div class="header-title">One Column</div>
  <div class="abs" style="left:14px;top:34px;width:255px">
    <div class="h4">Lorem Ipsum</div>
    <ul class="bullets">
      <li>Lorem ipsum dolor sit amet, te ullum corpora delicata duo. Rebum insolens pri eu. No alia tota modus qui.</li><li class="sub">Sint brute at usu. Duo iisque apparat adversarium at.</li>
      <li>Lorem ipsum dolor sit amet, te ullum corpora delicata duo. Rebum insolens pri eu. No alia tota modus qui.</li><li class="sub">Sint brute at usu. Duo iisque apparat adversarium at.</li>
      <li>Lorem ipsum dolor sit amet, te ullum corpora delicata duo. Rebum insolens pri eu. No alia tota modus qui.</li><li class="sub">Sint brute at usu. Duo iisque apparat adversarium at.</li>
      <li>Lorem ipsum dolor sit amet, te ullum corpora delicata duo. Rebum insolens pri eu. No alia tota modus qui.</li><li class="sub">Sint brute at usu. Duo iisque apparat adversarium at.</li>
    </ul>
  </div>
  <svg class="footer" viewBox="0 0 285 14"><polyline points="0,11 200,11 208,13 285,13" fill="none" stroke="var(--green)" stroke-width="1.2"/><polyline points="0,13 285,13" fill="none" stroke="var(--sky)" stroke-width=".8"/></svg>
  <div class="copy">Copyright © 2016 K Quadrant Advisory All rights reserved.</div>
  <div class="client">client logo here</div>
</section>

<!-- 7 two column -->
<section class="slide">
  <svg class="header" viewBox="0 0 285 24"><polygon points="40,4 285,4 285,20 32,20" fill="var(--charcoal)"/><rect x="272" y="6" width="8" height="6" fill="var(--sky)"/><rect x="0" y="21" width="285" height="1" fill="var(--sky)"/></svg>
  <div class="header-brand brand">K Quadrant</div>
  <div class="header-title">Two Column</div>
  <div class="abs" style="left:18px;top:38px;width:115px">
    <div class="h4">Lorem Ipsum</div>
    <ul class="bullets"><li>Lorem ipsum dolor sit amet, te ullum corpora delicata duo. Rebum insolens pri eu. No alia tota modus qui.</li><li class="sub">Sint brute at usu. Duo iisque apparat adversarium at.</li><li>Lorem ipsum dolor sit amet, te ullum corpora delicata duo. Rebum insolens pri eu. No alia tota modus qui.</li><li class="sub">Sint brute at usu. Duo iisque apparat adversarium at.</li><li>Lorem ipsum dolor sit amet, te ullum corpora delicata duo. Rebum insolens pri eu. No alia tota modus qui.</li></ul>
  </div>
  <div class="abs" style="left:148px;top:38px;width:115px">
    <div class="h4">Lorem Ipsum</div>
    <ul class="bullets"><li>Lorem ipsum dolor sit amet, te ullum corpora delicata duo. Rebum insolens pri eu. No alia tota modus qui.</li><li class="sub">Sint brute at usu. Duo iisque apparat adversarium at.</li><li>Lorem ipsum dolor sit amet, te ullum corpora delicata duo. Rebum insolens pri eu. No alia tota modus qui.</li><li class="sub">Sint brute at usu. Duo iisque apparat adversarium at.</li><li>Lorem ipsum dolor sit amet, te ullum corpora delicata duo. Rebum insolens pri eu. No alia tota modus qui.</li></ul>
  </div>
  <svg class="footer" viewBox="0 0 285 14"><polyline points="0,11 200,11 208,13 285,13" fill="none" stroke="var(--green)" stroke-width="1.2"/><polyline points="0,13 285,13" fill="none" stroke="var(--sky)" stroke-width=".8"/></svg>
  <div class="copy">Copyright © 2016 K Quadrant Advisory All rights reserved.</div>
  <div class="client">client logo here</div>
</section>

<!-- 8 left column -->
<section class="slide">
  <svg class="header" viewBox="0 0 285 24"><polygon points="40,4 285,4 285,20 32,20" fill="var(--charcoal)"/><rect x="272" y="6" width="8" height="6" fill="var(--sky)"/><rect x="0" y="21" width="285" height="1" fill="var(--sky)"/></svg>
  <div class="header-brand brand">K Quadrant</div>
  <div class="header-title">Left Column</div>
  <div class="abs" style="left:18px;top:38px;width:118px">
    <div class="h4">Lorem Ipsum</div>
    <ul class="bullets"><li>Lorem ipsum dolor sit amet, te ullum corpora delicata duo. Rebum insolens pri eu. No alia tota modus qui.</li><li class="sub">Sint brute at usu. Duo iisque apparat adversarium at.</li><li>Lorem ipsum dolor sit amet, te ullum corpora delicata duo. Rebum insolens pri eu. No alia tota modus qui.</li><li class="sub">Sint brute at usu. Duo iisque apparat adversarium at.</li><li>Lorem ipsum dolor sit amet, te ullum corpora delicata duo. Rebum insolens pri eu. No alia tota modus qui.</li></ul>
  </div>
  <svg class="abs" style="left:150px;top:38px" width="125" height="100" viewBox="0 0 125 100">
    <polygon points="62,0 73,20 51,20" fill="#d4d4d4"/>
    <polygon points="50,23 74,23 86,45 38,45" fill="var(--navy)"/>
    <polygon points="37,48 87,48 99,70 25,70" fill="var(--sky)"/>
    <polygon points="24,73 100,73 113,97 11,97" fill="var(--green)"/>
  </svg>
  <svg class="footer" viewBox="0 0 285 14"><polyline points="0,11 200,11 208,13 285,13" fill="none" stroke="var(--green)" stroke-width="1.2"/><polyline points="0,13 285,13" fill="none" stroke="var(--sky)" stroke-width=".8"/></svg>
  <div class="copy">Copyright © 2016 K Quadrant Advisory All rights reserved.</div>
  <div class="client">client logo here</div>
</section>

<!-- 9 right column with image, full bleed -->
<section class="slide">
  <div class="photo" style="left:0;top:0;width:140px;height:159px" role="img" aria-label="Portrait photo of a smiling doctor in a white coat with a stethoscope"></div>
  <div class="abs" style="left:147px;top:16px;font-size:9px;font-weight:700;color:#111">Right Column With Image</div>
  <div class="abs" style="left:151px;top:37px;width:122px">
    <div class="h4" style="color:var(--green)">Lorem Ipsum</div>
    <ul class="bullets"><li>Lorem ipsum dolor sit amet, te ullum corpora delicata duo. Rebum insolens pri eu. No alia tota modus qui.</li><li class="sub">Sint brute at usu. Duo iisque apparat adversarium at.</li><li>Lorem ipsum dolor sit amet, te ullum corpora delicata duo. Rebum insolens pri eu. No alia tota modus qui.</li><li class="sub">Sint brute at usu. Duo iisque apparat adversarium at.</li><li>Lorem ipsum dolor sit amet, te ullum corpora delicata duo. Rebum insolens pri eu. No alia tota modus qui.</li></ul>
  </div>
  <svg class="footer" viewBox="0 0 285 14"><polyline points="140,11 200,11 208,13 285,13" fill="none" stroke="var(--green)" stroke-width="1.2"/><polyline points="140,13 285,13" fill="none" stroke="var(--sky)" stroke-width=".8"/></svg>
  <div class="client">client logo here</div>
</section>

<!-- 10 right column with image, header -->
<section class="slide">
  <svg class="header" viewBox="0 0 285 24"><polygon points="40,4 285,4 285,20 32,20" fill="var(--charcoal)"/><rect x="272" y="6" width="8" height="6" fill="var(--sky)"/><rect x="0" y="21" width="285" height="1" fill="var(--sky)"/></svg>
  <div class="header-brand brand">K Quadrant</div>
  <div class="header-title">Right Column With Image</div>
  <div class="photo" style="left:0;top:22px;width:110px;height:137px" role="img" aria-label="Photo of a smiling doctor with arms crossed"></div>
  <div class="abs" style="left:145px;top:38px;width:125px">
    <div class="h4" style="color:var(--green)">Lorem Ipsum</div>
    <ul class="bullets"><li>Lorem ipsum dolor sit amet, te ullum corpora delicata duo. Rebum insolens pri eu. No alia tota modus qui.</li><li class="sub">Sint brute at usu. Duo iisque apparat adversarium at.</li><li>Lorem ipsum dolor sit amet, te ullum corpora delicata duo. Rebum insolens pri eu. No alia tota modus qui.</li><li class="sub">Sint brute at usu. Duo iisque apparat adversarium at.</li><li>Lorem ipsum dolor sit amet, te ullum corpora delicata duo. Rebum insolens pri eu. No alia tota modus qui.</li></ul>
  </div>
  <svg class="footer" viewBox="0 0 285 14"><polyline points="110,11 200,11 208,13 285,13" fill="none" stroke="var(--green)" stroke-width="1.2"/><polyline points="110,13 285,13" fill="none" stroke="var(--sky)" stroke-width=".8"/></svg>
  <div class="copy">Copyright © 2016 K Quadrant Advisory All rights reserved.</div>
  <div class="client">client logo here</div>
</section>

<!-- 11 team -->
<section class="slide">
  <svg class="header" viewBox="0 0 285 24"><polygon points="40,4 285,4 285,20 32,20" fill="var(--charcoal)"/><rect x="272" y="6" width="8" height="6" fill="var(--sky)"/><rect x="0" y="21" width="285" height="1" fill="var(--sky)"/></svg>
  <div class="header-brand brand">K Quadrant</div>
  <div class="header-title">Our Team</div>
  <div class="member" style="left:40px;top:33px"><div class="avatar" role="img" aria-label="Team member portrait"></div><div class="name">Alex Moran</div><div class="role">Doctor</div></div>
  <div class="member" style="left:123px;top:33px"><div class="avatar" role="img" aria-label="Team member portrait"></div><div class="name">Alex Moran</div><div class="role">Doctor</div></div>
  <div class="member" style="left:206px;top:33px"><div class="avatar" role="img" aria-label="Team member portrait"></div><div class="name">Alex Moran</div><div class="role">Doctor</div></div>
  <div class="member" style="left:40px;top:90px"><div class="avatar" role="img" aria-label="Team member portrait"></div><div class="name">Alex Moran</div><div class="role">Doctor</div></div>
  <div class="member" style="left:123px;top:90px"><div class="avatar" role="img" aria-label="Team member portrait"></div><div class="name">Alex Moran</div><div class="role">Doctor</div></div>
  <div class="member" style="left:206px;top:90px"><div class="avatar" role="img" aria-label="Team member portrait"></div><div class="name">Alex Moran</div><div class="role">Doctor</div></div>
  <svg class="footer" viewBox="0 0 285 14"><polyline points="0,11 200,11 208,13 285,13" fill="none" stroke="var(--green)" stroke-width="1.2"/><polyline points="0,13 285,13" fill="none" stroke="var(--sky)" stroke-width=".8"/></svg>
  <div class="copy">Copyright © 2016 K Quadrant Advisory All rights reserved.</div>
  <div class="client">client logo here</div>
</section>

<!-- 12 table -->
<section class="slide">
  <svg class="header" viewBox="0 0 285 24"><polygon points="40,4 285,4 285,20 32,20" fill="var(--charcoal)"/><rect x="272" y="6" width="8" height="6" fill="var(--sky)"/><rect x="0" y="21" width="285" height="1" fill="var(--sky)"/></svg>
  <div class="header-brand brand">K Quadrant</div>
  <div class="header-title">Table Sample</div>
  <table class="data">
    <tr><th style="background:var(--green)">Lorem ipsum</th><th style="background:var(--sky)">Lorem ipsum 1</th><th style="background:var(--navy)">Lorem ipsum 2</th><th style="background:var(--grey)">Lorem ipsum 3</th></tr>
    <tr><td>• Lorem ipsum dolor sit amet, consectetur adipiscing elit.</td><td>• Lorem ipsum dolor sit amet, consectetur elit.</td><td>• Lorem ipsum dolor sit amet, consectetur elit.</td><td>• Lorem ipsum dolor sit amet, consectetur elit.</td></tr>
    <tr><td>• Lorem ipsum dolor sit amet, consectetur elit.</td><td>• Lorem ipsum dolor sit amet, consectetur elit.</td><td>• Lorem ipsum dolor sit amet, quisque non enim.</td><td>• Lorem ipsum dolor sit amet, consectetur elit.</td></tr>
    <tr><td>• Lorem ipsum dolor sit amet, consectetur elit.</td><td>• Lorem ipsum dolor sit amet, consectetur elit.</td><td>• Lorem ipsum dolor sit amet, consectetur elit.</td><td>• Lorem ipsum dolor sit amet, consectetur elit.</td></tr>
    <tr><td>• Lorem ipsum dolor sit amet, consectetur elit.</td><td>• Lorem ipsum dolor sit amet, consectetur elit.</td><td>• Lorem ipsum dolor sit amet, consectetur elit.</td><td>• Lorem ipsum dolor sit amet, consectetur elit.</td></tr>
  </table>
  <svg class="footer" viewBox="0 0 285 14"><polyline points="0,11 200,11 208,13 285,13" fill="none" stroke="var(--green)" stroke-width="1.2"/><polyline points="0,13 285,13" fill="none" stroke="var(--sky)" stroke-width=".8"/></svg>
  <div class="copy">Copyright © 2016 K Quadrant Advisory All rights reserved.</div>
  <div class="client">client logo here</div>
</section>

<!-- 13 about -->
<section class="slide">
  <svg class="header" viewBox="0 0 285 24"><polygon points="40,4 285,4 285,20 32,20" fill="var(--charcoal)"/><rect x="272" y="6" width="8" height="6" fill="var(--sky)"/><rect x="0" y="21" width="285" height="1" fill="var(--sky)"/></svg>
  <div class="header-brand brand">K Quadrant</div>
  <div class="header-title">About Us</div>
  <div class="photo" style="left:16px;top:44px;width:88px;height:88px;border-radius:50%" role="img" aria-label="Circular portrait photo of a smiling doctor"></div>
  <div class="abs" style="left:116px;top:40px;width:160px">
    <div class="h4">Lorem Ipsum is simply dummy</div>
    <p class="txt" style="font-size:3.9px">Text of the printing and typesetting industry. Lorem Ipsum has been the industry's standard dummy text ever since the 1500s, when an unknown printer took a galley of type and scrambled it to make a type specimen book. It has survived not only five centuries, but also the leap into electronic typesetting, remaining essentially unchanged. It was popularised in the 1960s with the release of sheets containing passages, and more recently with desktop publishing software.</p>
    <p class="txt" style="font-size:3.9px;margin-top:2px">Lorem Ipsum has been the industry's standard dummy text ever since the 1500s, when an unknown printer took a galley of type and scrambled it.</p>
  </div>
  <svg class="footer" viewBox="0 0 285 14"><polyline points="0,11 200,11 208,13 285,13" fill="none" stroke="var(--green)" stroke-width="1.2"/><polyline points="0,13 285,13" fill="none" stroke="var(--sky)" stroke-width=".8"/></svg>
  <div class="copy">Copyright © 2016 K Quadrant Advisory All rights reserved.</div>
  <div class="client">client logo here</div>
</section>

<!-- 14 pie -->
<section class="slide">
  <svg class="header" viewBox="0 0 285 24"><polygon points="40,4 285,4 285,20 32,20" fill="var(--charcoal)"/><rect x="272" y="6" width="8" height="6" fill="var(--sky)"/><rect x="0" y="21" width="285" height="1" fill="var(--sky)"/></svg>
  <div class="header-brand brand">K Quadrant</div>
  <div class="header-title">Pie Chart Sample</div>
  <div class="abs" style="left:0;top:36px;width:285px;text-align:center;font-size:7px;font-weight:600">Lorem ipsum dolar sit amet</div>
  <svg class="abs" style="left:105px;top:50px" width="80" height="80" viewBox="0 0 42 42">
    <g transform="rotate(-90 21 21)">
      <circle cx="21" cy="21" r="10" fill="none" stroke="var(--green)" stroke-width="20" stroke-dasharray="36.4 62.8"/>
      <circle cx="21" cy="21" r="10" fill="none" stroke="var(--sky)" stroke-width="20" stroke-dasharray="0 36.4 14.4 62.8"/>
      <circle cx="21" cy="21" r="10" fill="none" stroke="var(--navy)" stroke-width="20" stroke-dasharray="0 50.8 6.3 62.8"/>
      <circle cx="21" cy="21" r="10" fill="none" stroke="#e3e3e3" stroke-width="20" stroke-dasharray="0 57.1 5.7 62.8"/>
    </g>
    <g font-size="2.2" fill="#fff" font-family="Open Sans, sans-serif"><text x="29" y="25">58%</text><text x="9" y="26">23%</text><text x="11" y="16">10%</text><text x="16.5" y="9" fill="#777">9%</text></g>
  </svg>
  <div class="abs" style="left:70px;top:138px;font-size:3.4px;color:#777;word-spacing:2px"><span style="color:var(--green)">●</span> Lorem Ipsum &nbsp; <span style="color:var(--sky)">●</span> Lorem Ipsum &nbsp; <span style="color:var(--navy)">●</span> Lorem Ipsum &nbsp; <span style="color:#ccc">●</span> Lorem Ipsum</div>
  <svg class="footer" viewBox="0 0 285 14"><polyline points="0,11 200,11 208,13 285,13" fill="none" stroke="var(--green)" stroke-width="1.2"/><polyline points="0,13 285,13" fill="none" stroke="var(--sky)" stroke-width=".8"/></svg>
  <div class="copy">Copyright © 2016 K Quadrant Advisory All rights reserved.</div>
  <div class="client">client logo here</div>
</section>

<!-- 15 chevron -->
<section class="slide">
  <svg class="header" viewBox="0 0 285 24"><polygon points="40,4 285,4 285,20 32,20" fill="var(--charcoal)"/><rect x="272" y="6" width="8" height="6" fill="var(--sky)"/><rect x="0" y="21" width="285" height="1" fill="var(--sky)"/></svg>
  <div class="header-brand brand">K Quadrant</div>
  <div class="header-title">Basic Chevron Process</div>
  <svg class="abs" style="left:20px;top:39px" width="250" height="34" viewBox="0 0 250 34">
    <polygon points="0,0 80,0 90,17 80,34 0,34" fill="var(--green)"/>
    <polygon points="78,0 160,0 170,17 160,34 78,34 88,17" fill="var(--sky)"/>
    <polygon points="158,0 240,0 250,17 240,34 158,34 168,17" fill="var(--navy)"/>
    <g fill="#fff" font-size="6.5" font-family="Open Sans, sans-serif"><text x="20" y="20">Lorem ipsum</text><text x="100" y="20">Lorem ipsum</text><text x="178" y="20">Lorem ipsum</text></g>
  </svg>
  <div class="abs" style="left:24px;top:82px;width:68px"><ul class="bullets"><li>Lorem ipsum dolor sit amet, consectetur adipiscing elit</li><li>Nunc quis dui dolor</li><li>Maecenas sem nibh, congue a urna non, volutpat porttitor justo</li></ul></div>
  <div class="abs" style="left:104px;top:82px;width:68px"><ul class="bullets"><li>Lorem ipsum dolor sit amet, consectetur adipiscing elit</li><li>Nunc quis dui dolor</li><li>Maecenas sem nibh, congue a urna non, volutpat porttitor justo</li></ul></div>
  <div class="abs" style="left:184px;top:82px;width:68px"><ul class="bullets"><li>Lorem ipsum dolor sit amet, consectetur adipiscing elit</li><li>Nunc quis dui dolor</li><li>Maecenas sem nibh, congue a urna non, volutpat porttitor justo</li></ul></div>
  <svg class="footer" viewBox="0 0 285 14"><polyline points="0,11 200,11 208,13 285,13" fill="none" stroke="var(--green)" stroke-width="1.2"/><polyline points="0,13 285,13" fill="none" stroke="var(--sky)" stroke-width=".8"/></svg>
  <div class="copy">Copyright © 2016 K Quadrant Advisory All rights reserved.</div>
  <div class="client">client logo here</div>
</section>

<!-- 16 venn -->
<section class="slide">
  <svg class="header" viewBox="0 0 285 24"><polygon points="40,4 285,4 285,20 32,20" fill="var(--charcoal)"/><rect x="272" y="6" width="8" height="6" fill="var(--sky)"/><rect x="0" y="21" width="285" height="1" fill="var(--sky)"/></svg>
  <div class="header-brand brand">K Quadrant</div>
  <div class="header-title">Linier VEEN</div>
  <svg class="abs" style="left:35px;top:37px" width="220" height="82" viewBox="0 0 220 82">
    <circle cx="41" cy="41" r="40" fill="var(--green)" opacity=".9"/>
    <circle cx="110" cy="41" r="40" fill="var(--sky)" opacity=".85"/>
    <circle cx="179" cy="41" r="40" fill="var(--navy)" opacity=".8"/>
  </svg>
  <div class="center-copy txt" style="left:50px;top:54px;width:52px;color:#fff;font-size:3.7px">Lorem ipsum dolor sit amet, consectetur adipiscing elit. Nunc quis dui dolor. Maecenas sem nibh, congue a urna non, volutpat porttitor justo.</div>
  <div class="center-copy txt" style="left:119px;top:54px;width:52px;color:#fff;font-size:3.7px">Lorem ipsum dolor sit amet, consectetur adipiscing elit. Nunc quis dui dolor. Maecenas sem nibh, congue a urna non, volutpat porttitor justo.</div>
  <div class="center-copy txt" style="left:188px;top:54px;width:52px;color:#fff;font-size:3.7px">Lorem ipsum dolor sit amet, consectetur adipiscing elit. Nunc quis dui dolor. Maecenas sem nibh, congue a urna non, volutpat porttitor justo.</div>
  <svg class="footer" viewBox="0 0 285 14"><polyline points="0,11 200,11 208,13 285,13" fill="none" stroke="var(--green)" stroke-width="1.2"/><polyline points="0,13 285,13" fill="none" stroke="var(--sky)" stroke-width=".8"/></svg>
  <div class="copy">Copyright © 2016 K Quadrant Advisory All rights reserved.</div>
  <div class="client">client logo here</div>
</section>

<!-- 17 bar chart -->
<section class="slide">
  <svg class="header" viewBox="0 0 285 24"><polygon points="40,4 285,4 285,20 32,20" fill="var(--charcoal)"/><rect x="272" y="6" width="8" height="6" fill="var(--sky)"/><rect x="0" y="21" width="285" height="1" fill="var(--sky)"/></svg>
  <div class="header-brand brand">K Quadrant</div>
  <div class="header-title">Bar Chart Sample</div>
  <div class="abs" style="left:0;top:34px;width:285px;text-align:center;font-size:6.5px;font-weight:600">Lorem ipsum dolor sit amet</div>
  <svg class="abs" style="left:20px;top:47px" width="250" height="90" viewBox="0 0 250 90">
    <g fill="#888" font-size="3.3" font-family="Open Sans, sans-serif"><text x="0" y="4">6</text><text x="0" y="17">5</text><text x="0" y="30">4</text><text x="0" y="43">3</text><text x="0" y="56">2</text><text x="0" y="69">1</text><text x="0" y="82">0</text></g>
    <line x1="6" y1="81" x2="245" y2="81" stroke="#ccc" stroke-width=".5"/>
    <line x1="6" y1="2" x2="6" y2="81" stroke="#ccc" stroke-width=".5"/>
    <rect x="12" y="26" width="8" height="55" fill="var(--green)"/>
    <rect x="32" y="46" width="8" height="35" fill="var(--sky)"/>
    <rect x="52" y="37" width="8" height="44" fill="var(--green)"/>
    <rect x="72" y="58" width="8" height="23" fill="var(--grey)"/>
    <rect x="92" y="23" width="8" height="58" fill="var(--sky)"/>
    <rect x="112" y="51" width="8" height="30" fill="var(--sky)"/>
    <rect x="132" y="65" width="8" height="16" fill="var(--sky)"/>
    <rect x="152" y="8" width="8" height="73" fill="var(--navy)"/>
    <rect x="172" y="44" width="8" height="37" fill="var(--navy)"/>
    <rect x="192" y="59" width="8" height="22" fill="var(--navy)"/>
    <rect x="212" y="33" width="8" height="48" fill="var(--grey)"/>
    <g fill="#888" font-size="2.8" font-family="Open Sans, sans-serif"><text x="8" y="87">Category 1</text><text x="48" y="87">Category 3</text><text x="88" y="87">Category 5</text><text x="128" y="87">Category 7</text><text x="168" y="87">Category 9</text><text x="208" y="87">Category 11</text></g>
  </svg>
  <svg class="footer" viewBox="0 0 285 14"><polyline points="0,11 200,11 208,13 285,13" fill="none" stroke="var(--green)" stroke-width="1.2"/><polyline points="0,13 285,13" fill="none" stroke="var(--sky)" stroke-width=".8"/></svg>
  <div class="copy">Copyright © 2016 K Quadrant Advisory All rights reserved.</div>
  <div class="client">client logo here</div>
</section>

<!-- 18 graphic -->
<section class="slide">
  <svg class="header" viewBox="0 0 285 24"><polygon points="40,4 285,4 285,20 32,20" fill="var(--charcoal)"/><rect x="272" y="6" width="8" height="6" fill="var(--sky)"/><rect x="0" y="21" width="285" height="1" fill="var(--sky)"/></svg>
  <div class="header-brand brand">K Quadrant</div>
  <div class="header-title">Graphic Sample</div>
  <svg class="abs" style="left:102px;top:42px" width="80" height="90" viewBox="0 0 80 90">
    <circle cx="40" cy="45" r="32" fill="none" stroke="var(--green)" stroke-width="1.2"/>
    <g fill="#fff" stroke="var(--green)" stroke-width="1.2">
      <circle cx="40" cy="13" r="7"/><circle cx="68" cy="29" r="7"/><circle cx="68" cy="61" r="7"/>
      <circle cx="40" cy="77" r="7"/><circle cx="12" cy="61" r="7"/><circle cx="12" cy="29" r="7"/>
    </g>
    <g fill="none" stroke="var(--sky)" stroke-width=".9">
      <circle cx="40" cy="13" r="3"/><path d="M66 27h4v4h-4z"/><path d="M65 61h6M68 58v6"/>
      <rect x="38" y="74" width="4" height="6" rx=".6"/><circle cx="12" cy="61" r="2.5"/><rect x="9" y="27" width="6" height="4"/>
    </g>
    <text x="40" y="44" text-anchor="middle" font-size="4.5" font-weight="700" fill="var(--navy)" font-family="Open Sans, sans-serif">K Quadrant</text>
    <text x="40" y="50" text-anchor="middle" font-size="4.5" font-weight="700" fill="var(--navy)" font-family="Open Sans, sans-serif">Advisory</text>
  </svg>
  <div class="abs txt" style="left:113px;top:30px;width:60px;text-align:center;font-size:3.6px">Lorem ipsum dolor sit amet, consectetur adipiscing elit</div>
  <div class="abs txt" style="left:43px;top:57px;width:60px;text-align:right;font-size:3.6px">Lorem ipsum dolor sit amet, consectetur adipiscing elit</div>
  <div class="abs txt" style="left:187px;top:57px;width:60px;font-size:3.6px">Lorem ipsum dolor sit amet, consectetur adipiscing elit</div>
  <div class="abs txt" style="left:43px;top:97px;width:60px;text-align:right;font-size:3.6px">Lorem ipsum dolor sit amet, consectetur adipiscing elit</div>
  <div class="abs txt" style="left:187px;top:97px;width:60px;font-size:3.6px">Lorem ipsum dolor sit amet, consectetur adipiscing elit</div>
  <div class="abs txt" style="left:113px;top:133px;width:60px;text-align:center;font-size:3.6px">Lorem ipsum dolor sit amet, consectetur adipiscing elit</div>
  <svg class="footer" viewBox="0 0 285 14"><polyline points="0,11 200,11 208,13 285,13" fill="none" stroke="var(--green)" stroke-width="1.2"/><polyline points="0,13 285,13" fill="none" stroke="var(--sky)" stroke-width=".8"/></svg>
  <div class="client">client logo here</div>
</section>

<!-- 19 content with icons -->
<section class="slide">
  <div class="photo photo-dark" style="left:0;top:0;width:285px;height:100px" role="img" aria-label="Photo of a doctor talking with a patient, darkened behind the title"></div>
  <div class="abs" style="left:0;top:0;width:285px;height:100px;background:linear-gradient(180deg,rgba(255,255,255,0) 55%,#fff 100%)"></div>
  <div class="center-copy" style="left:0;top:6px;width:285px;font-size:9px;font-weight:700">Content With Icon Sample</div>
  <div class="abs" style="left:268px;top:4px;width:8px;height:6px;background:var(--sky)"></div>
  <div class="icon-card" style="left:17px;top:85px"><div class="dot" style="border:1.3px solid var(--green)"><svg width="10" height="10" viewBox="0 0 10 10"><circle cx="4" cy="4" r="3" fill="none" stroke="var(--green)" stroke-width="1.2"/><path d="M6 6l3 3" stroke="var(--green)" stroke-width="1.4"/></svg></div><div class="h" style="color:var(--green)">Lorem Ipsum</div><div class="t">Lorem ipsum dolor sit amet, consectetur adipiscing elit</div></div>
  <div class="icon-card" style="left:83px;top:85px"><div class="dot" style="border:1.3px solid var(--sky)"><svg width="10" height="10" viewBox="0 0 10 10"><rect x="1" y="1.5" width="8" height="5.5" fill="none" stroke="var(--sky)" stroke-width="1"/><path d="M3 9h4M5 7v2" stroke="var(--sky)" stroke-width="1"/></svg></div><div class="h">Lorem Ipsum</div><div class="t">Lorem ipsum dolor sit amet, consectetur adipiscing elit</div></div>
  <div class="icon-card" style="left:148px;top:85px"><div class="dot" style="background:var(--navy)"><svg width="10" height="10" viewBox="0 0 10 10"><circle cx="5" cy="5" r="3" fill="none" stroke="#fff" stroke-width="1.4" stroke-dasharray="1.5 .8"/><circle cx="5" cy="5" r="1" fill="#fff"/></svg></div><div class="h" style="color:var(--navy)">Lorem Ipsum</div><div class="t">Lorem ipsum dolor sit amet, consectetur adipiscing elit</div></div>
  <div class="icon-card" style="left:214px;top:85px"><div class="dot" style="border:1.3px solid #999"><svg width="10" height="10" viewBox="0 0 10 10"><path d="M2 8l6-6M2 2l6 6" stroke="#777" stroke-width="1.2"/></svg></div><div class="h" style="color:#666">Lorem Ipsum</div><div class="t">Lorem ipsum dolor sit amet, consectetur adipiscing elit</div></div>
  <svg class="footer" viewBox="0 0 285 14"><polyline points="0,11 200,11 208,13 285,13" fill="none" stroke="var(--green)" stroke-width="1.2"/><polyline points="0,13 285,13" fill="none" stroke="var(--sky)" stroke-width=".8"/></svg>
  <div class="copy">Copyright © 2016 K Quadrant Advisory All rights reserved.</div>
  <div class="client">client logo here</div>
</section>

<!-- 20 testimonials -->
<section class="slide">
  <div class="photo photo-dark" style="inset:0" role="img" aria-label="Darkened photo of a doctor in conversation with a patient"></div>
  <div class="center-copy" style="left:0;top:6px;width:285px;font-size:9px;font-weight:700">Testimonials</div>
  <div class="abs" style="left:268px;top:4px;width:8px;height:6px;background:var(--sky)"></div>
  <svg class="abs" style="left:130px;top:38px" width="25" height="25" viewBox="0 0 25 25"><circle cx="12.5" cy="12.5" r="11" fill="none" stroke="var(--green)" stroke-width="1.3"/><text x="12.5" y="17" text-anchor="middle" font-size="11" font-weight="700" font-style="italic" fill="var(--green)" font-family="Open Sans, sans-serif">”</text></svg>
  <div class="center-copy" style="left:20px;top:82px;width:245px;font-size:4.5px;line-height:1.4">Lorem Ipsum is simply dummy text of the printing and typesetting industry. Lorem Ipsum has been the industry's standard dummy text ever since the 1500s, when an unknown printer took a galley of type and scrambled it to make a type specimen book.</div>
  <div class="center-copy" style="left:0;top:112px;width:285px;font-size:5px;font-weight:700;font-style:italic">- Alex Moran -</div>
  <div class="copy" style="color:#ccc">Copyright © 2016 K Quadrant Advisory All rights reserved.</div>
</section>

<!-- 21 thank you -->
<section class="slide">
  <svg class="abs" style="left:0;top:0" width="285" height="159" viewBox="0 0 285 159">
    <rect x="0" y="0" width="285" height="7" fill="var(--navy)"/>
    <polyline points="0,11 130,11 140,16 285,16" fill="none" stroke="var(--sky)" stroke-width="1.5"/>
    <polygon points="0,142 170,142 182,150 285,150 285,159 0,159" fill="var(--green)"/>
    <polygon points="0,152 285,152 285,159 0,159" fill="var(--sky)"/>
    <polygon points="0,156 285,156 285,159 0,159" fill="var(--navy)"/>
  </svg>
  <div class="abs" style="left:8px;top:46px;font-size:8.5px;font-weight:700;color:#111">THANK YOU FONT 24PT</div>
  <div class="abs" style="left:9px;top:64px;font-size:3.6px;line-height:1.35;color:#555">
    <b style="color:#111;font-size:4px">ADDRESS</b><br>Lorem ipsum<br>
    <b style="color:#111;font-size:4px">PHONE/FAX</b><br>Call 555-014-2290<br>Fax 555-014-2291<br>
    <b style="color:#111;font-size:4px">EMAIL</b><br>dorrit@kquadrantadvisory.co<br>
    <b style="color:#111;font-size:4px">WEBSITE</b><br>www.kquadrantadvisory.co
  </div>
  <div class="abs brand" style="left:200px;top:52px;font-size:6px;width:60px;text-align:center">K Quadrant Advisory</div>
  <div class="abs txt" style="left:180px;top:82px;width:96px;font-size:3.6px;text-align:center">Lorem Ipsum is simply dummy text of the printing and typesetting industry. Lorem Ipsum has been the industry's standard dummy text ever since the 1500s, when an unknown printer took a galley of type and scrambled it to make a type specimen. The industry's standard dummy text ever since the 1500s.</div>
</section>

</main>
</body>
</html>
```